Telecommunications/Power civil contractor needs business card design

Were a new telecommunications/power underground civil contractor that is looking for a new business card design. Our company colours are silver or grey and orange. Feel free to use the white background logo or the black background logo.

Target Market(s)

Local contractors, utility companies, private sector mining/energy companies, developers.

Industry/Entity Type

Telecommunications

Contact Information for Business Card

Each card will need the following info:
Persons name:
Title:
E-mail:
Phone number:
Shop Address:
Mailing Address:

Requirements
Must have
• Each card will need the following info:
• Persons name:
• Title:
• E-mail:
• Phone number:
• Shop Address:
• Mailing Address:

```html
<!DOCTYPE html>
<html lang="en">
<head>
<meta charset="utf-8">
<title>Ridgeline Contracting Inc – Business Card</title>
<link rel="stylesheet" href="https://fonts.googleapis.com/css2?family=Open+Sans:wght@400;600;700;800&display=swap">
<style>
  :root {
    --brand-orange: #f05a24;
    --brand-grey: #6b6b6b;
    --ink: #1e1e1e;
    --paper: #ffffff;
    --backdrop: #e9e7e4;
  }
  * { margin: 0; padding: 0; box-sizing: border-box; }
  html, body { width: 1200px; height: 900px; overflow: hidden; }
  body {
    background: var(--backdrop);
    font-family: "Open Sans", Arial, sans-serif;
    position: relative;
  }
  .card { position: absolute; }
  .card-shape { position: absolute; left: 0; top: 0; display: block; }
  .card-front { left: 77px; top: 35px; width: 590px; height: 362px; }
  .card-back { left: 390px; top: 505px; width: 566px; height: 354px; }

  .holder-name {
    position: absolute; left: 28px; top: 36px;
    color: var(--paper); font-size: 22px; font-weight: 700;
  }
  .holder-title {
    position: absolute; left: 28px; top: 64px;
    color: var(--paper); font-size: 16px; font-weight: 400;
  }
  .address-block { position: absolute; left: 31px; color: var(--ink); font-size: 15.5px; line-height: 19px; }
  .address-block.shop { top: 120px; }
  .address-block.mailing { top: 191px; }
  .address-label { color: var(--brand-orange); font-size: 17.5px; font-weight: 600; line-height: 22px; }

  .contact-list { position: absolute; left: 30px; top: 291px; list-style: none; color: var(--paper); font-size: 15.5px; }
  .contact-list li { display: flex; align-items: center; gap: 9px; height: 24px; }
  .contact-list svg { width: 11px; height: 11px; fill: var(--paper); }

  .front-mark {
    position: absolute; left: 330px; top: 162px; width: 172px;
    text-align: center; color: var(--brand-orange);
    font-size: 24px; font-weight: 800; letter-spacing: 1px;
  }
  .company-name {
    position: absolute; left: 258px; top: 140px;
    color: var(--brand-orange); font-weight: 800;
    font-size: 30px; line-height: 32px; letter-spacing: 1px;
  }
  .company-name span { display: block; font-size: 18px; line-height: 24px; letter-spacing: 1.5px; }
</style>
</head>
<body>

<section class="card card-front" aria-label="Business card, contact side">
  <svg class="card-shape" width="590" height="362" viewBox="0 0 590 362" aria-hidden="true">
    <rect x="0" y="0" width="420" height="362" fill="var(--brand-orange)"/>
    <circle cx="418" cy="182" r="170" fill="var(--brand-orange)"/>
    <rect x="0" y="102" width="420" height="156" fill="var(--paper)"/>
    <circle cx="418" cy="182" r="165" fill="var(--paper)"/>
  </svg>
  <h1 class="holder-name">Daniel Harper</h1>
  <p class="holder-title">Managing Director</p>
  <div class="address-block shop">
    <p class="address-label">Shop Address</p>
    <p>12345, Address Goes Here</p>
    <p>Country Name, 123456</p>
  </div>
  <div class="address-block mailing">
    <p class="address-label">Mailing Address</p>
    <p>12345, Address Goes Here</p>
    <p>Country Name, 123456</p>
  </div>
  <ul class="contact-list">
    <li>
      <svg viewBox="0 0 24 24" aria-hidden="true"><path d="M6.6 10.8a15.1 15.1 0 0 0 6.6 6.6l2.2-2.2a1 1 0 0 1 1-.25 11.4 11.4 0 0 0 3.6.6 1 1 0 0 1 1 1V20a1 1 0 0 1-1 1A17 17 0 0 1 3 4a1 1 0 0 1 1-1h3.5a1 1 0 0 1 1 1c0 1.25.2 2.45.6 3.6a1 1 0 0 1-.25 1z"/></svg>
      (044)-555-0142
    </li>
    <li>
      <svg viewBox="0 0 24 24" aria-hidden="true"><path d="M2 5h20v14H2z M2 5l10 8 10-8" stroke="var(--brand-orange)" stroke-width="1.5"/></svg>
      info@ridgelinecivil.com
    </li>
  </ul>
  <p class="front-mark">RIDGELINE</p>
</section>

<section class="card card-back" aria-label="Business card, company side">
  <svg class="card-shape" width="566" height="354" viewBox="0 0 566 354" aria-hidden="true">
    <rect x="170" y="0" width="396" height="354" fill="var(--brand-orange)"/>
    <circle cx="172" cy="177" r="170" fill="var(--brand-orange)"/>
    <rect x="170" y="97" width="396" height="150" fill="var(--paper)"/>
    <circle cx="172" cy="177" r="165" fill="var(--paper)"/>
  </svg>
  <h2 class="company-name">RIDGELINE <span>CONTRACTING INC</span></h2>
</section>

</body>
</html>
```